Design a website for our small self storage business

We're looking for a freelance web designer who can produce a good-looking design for our small business website (no coding necessary). We will provide a list of pages to design, along with content outlines.

Key skills:
- Graphic design
- Responsive web design
- Proficiency with a modern web design tool such as Figma, Adobe Xd, or InVision

Please send relevant previous work (preferably in an inspectable format such as Figma or Invision).

```html
<!DOCTYPE html>
<html lang="en">
<head>
<meta charset="utf-8">
<title>Harbor Lane Self Storage</title>
<link href="https://fonts.googleapis.com/css2?family=Poppins:wght@400;500;600;700;800&display=swap" rel="stylesheet">
<style>
:root{
  --blue:#0d4f96;
  --navy:#0a4a8c;
  --navy-dark:#0b5299;
  --red:#e01b22;
  --gray:#efefef;
  --text:#444;
  --white:#fff;
}
*{margin:0;padding:0;box-sizing:border-box}
html,body{width:1200px;height:3428px;overflow:hidden}
body{position:relative;font-family:'Poppins',sans-serif;color:var(--text);background:var(--white)}
.abs{position:absolute}
.brand{font-weight:700;color:var(--blue);font-size:22px;line-height:1.1;text-align:center}
.brand small{display:block;font-size:13px;color:var(--red);letter-spacing:2px;font-weight:700}
.nav a{position:absolute;top:58px;font-size:16px;font-weight:500;color:#222;text-decoration:none;letter-spacing:.5px}
.nav a.active{color:var(--red);font-weight:600}
.call-icon{left:858px;top:45px;width:44px;height:44px;border-radius:50%;background:var(--blue)}
.call-label{left:910px;top:40px;font-size:17px;font-weight:700;color:#222}
.call-number{left:910px;top:62px;font-size:26px;font-weight:700;color:var(--red)}
.hero{left:0;top:133px;width:1200px;height:734px;background:linear-gradient(100deg,#8a5a48 0%,#b3302c 20%,#c52a28 45%,#b8494a 70%,#8f8e8d 100%)}
.hero-title{left:0;width:1200px;top:350px;text-align:center;color:#fff;font-size:58px;font-weight:800;line-height:56px;letter-spacing:1px}
.hero-btn{left:492px;top:541px;width:216px;height:56px;background:var(--red);border:2px solid #fff;color:#fff;font-weight:700;font-size:20px;display:flex;align-items:center;justify-content:center}
.dots{left:566px;top:689px;display:flex;gap:10px}
.dots span{width:10px;height:10px;border-radius:50%;background:#fff}
.dots span:first-child{background:var(--blue)}
.section-title{color:var(--blue);font-weight:700;text-align:center}
.rule{height:2px;background:var(--blue)}
.card{top:1015px;width:328px;height:313px;background:#fff;border-radius:8px;box-shadow:0 2px 12px rgba(0,0,0,.15);text-align:center}
.card.active{border:3px solid var(--red)}
.card .icon{width:120px;height:120px;border-radius:50%;background:linear-gradient(180deg,var(--red),var(--blue));margin:24px auto 0;display:flex;align-items:center;justify-content:center}
.card h3{color:var(--blue);font-size:23px;font-weight:600;margin-top:18px}
.card p{font-size:15px;line-height:28px;margin:8px 30px 0}
.body-text{font-size:17px;line-height:30.5px;text-align:center;color:#444}
.btn{background:var(--red);color:#fff;font-weight:700;font-size:18px;display:flex;align-items:center;justify-content:center}
.photo-frame{background:#fff;padding:6px;box-shadow:0 4px 14px rgba(0,0,0,.25)}
.photo-frame div{width:100%;height:100%}
.footer-head{font-size:18px;font-weight:600;color:#fff;letter-spacing:.5px}
.footer-link{font-size:16px;color:#fff}
.footer-line{font-size:16px;color:#fff;display:flex;gap:12px;align-items:flex-start}
.bottom-bar{left:0;top:3365px;width:1200px;height:63px;background:var(--navy-dark)}
.social{top:3382px;width:26px;height:26px;border-radius:50%;background:#fff}
</style>
</head>
<body>

<!-- Header -->
<div class="abs brand" style="left:60px;top:34px;width:200px">HARBOR LANE<small>SELF STORAGE</small></div>
<nav class="nav">
  <a class="active" style="left:403px">HOME</a>
  <a style="left:492px">UNITS</a>
  <a style="left:579px">PAY ONLINE</a>
  <a style="left:715px">CONTACT US</a>
</nav>
<div class="abs call-icon">
  <svg width="44" height="44" viewBox="0 0 44 44"><path d="M17 14c1 0 2 3 2 4s-2 2-2 3c1 3 3 5 6 6 1 0 2-2 3-2s4 1 4 2-1 3-3 4c-6 0-13-7-13-13 0-2 2-4 3-4z" fill="#fff"/></svg>
</div>
<div class="abs call-label">CALL US:</div>
<div class="abs call-number">1-800-555-0142</div>

<!-- Hero -->
<div class="abs hero" role="img" aria-label="Photo of a row of red roll-up storage unit doors"></div>
<svg class="abs" style="left:0;top:740px" width="1200" height="130"><polygon points="0,113 765,8 1200,127 1200,130 0,130" fill="#fff"/></svg>
<div class="abs hero-title">WELCOME TO<br>HARBOR LANE SELF STORAGE<br>IN FAIRVIEW</div>
<div class="abs hero-btn">SEE OUR UNITS</div>
<div class="abs dots"><span></span><span></span><span></span><span></span></div>

<!-- Key advantages -->
<div class="abs rule" style="left:316px;top:937px;width:88px"></div>
<div class="abs section-title" style="left:404px;top:912px;width:392px;font-size:39px">KEY ADVANTAGES</div>
<div class="abs rule" style="left:796px;top:937px;width:88px"></div>

<div class="abs card active" style="left:76px">
  <div class="icon"><svg width="56" height="56" viewBox="0 0 56 56" fill="none" stroke="#fff" stroke-width="2"><rect x="16" y="8" width="26" height="34" rx="2"/><path d="M21 16h16M21 22h16M21 28h10"/><circle cx="14" cy="40" r="7"/><circle cx="42" cy="42" r="6"/></svg></div>
  <h3>AFFORDABLE</h3>
  <p>Sed ut perspiciatis unde omnis iste natus error sit voluptatem accu santium doloremque.</p>
</div>
<div class="abs card" style="left:436px">
  <div class="icon"><svg width="56" height="56" viewBox="0 0 56 56" fill="none" stroke="#fff" stroke-width="2"><path d="M18 22v-6a10 10 0 0 1 20 0v6"/><rect x="12" y="22" width="32" height="24" rx="3"/><path d="M18 32h8M18 38h12"/><circle cx="42" cy="42" r="7"/><path d="M39 42l2 2 4-4"/></svg></div>
  <h3>SECURE</h3>
  <p>Sed ut perspiciatis unde omnis iste natus error sit voluptatem accu santium doloremque.</p>
</div>
<div class="abs card" style="left:798px">
  <div class="icon"><svg width="56" height="56" viewBox="0 0 56 56" fill="none" stroke="#fff" stroke-width="2"><circle cx="30" cy="18" r="9"/><path d="M8 38l10-6h12l8 4M8 46h16l20-10"/></svg></div>
  <h3>CONVENIENT</h3>
  <p>Sed ut perspiciatis unde omnis iste natus error sit voluptatem accu santium doloremque.</p>
</div>

<!-- Section: just show up -->
<svg class="abs" style="left:0;top:1377px" width="1200" height="745"><polygon points="0,0 426,120 1200,0 1200,618 426,744 0,618" fill="var(--gray)"/></svg>
<div class="abs" style="left:766px;top:1539px;width:361px;height:346px;background:var(--red)"></div>
<div class="abs photo-frame" style="left:705px;top:1571px;width:391px;height:517px">
  <div role="img" aria-label="Photo of a hand placing a box on a shelf" style="background:linear-gradient(160deg,#39516e,#c96a47 50%,#d9a35f)"></div>
</div>
<div class="abs rule" style="left:76px;top:1655px;width:88px"></div>
<div class="abs section-title" style="left:76px;top:1630px;width:602px;font-size:37px;line-height:49px">JUST SHOW UP WITH<br>YOUR STUFF</div>
<div class="abs rule" style="left:589px;top:1655px;width:88px"></div>
<p class="abs body-text" style="left:86px;top:1741px;width:582px">Sed ut perspiciatis unde omnis iste natus error sit voluptatem accusantium doloremque laudantium, totam rem aperiam, eaque ipsa quae ab illo inventore veritatis et quasi architecto beatae vitae dicta sunt explicabo. Nemo enim ipsam voluptatem quia voluptas sit aspernatur aut odit aut fugit, sed quia consequuntur magni dolores.</p>
<div class="abs btn" style="left:273px;top:1955px;width:207px;height:57px">READ MORE</div>

<!-- Section: what to bring -->
<div class="abs" style="left:76px;top:2193px;width:359px;height:345px;background:var(--red)"></div>
<div class="abs photo-frame" style="left:105px;top:2225px;width:391px;height:517px">
  <div role="img" aria-label="Photo of an indoor hallway lined with red storage lockers" style="background:linear-gradient(90deg,#b8242a,#d73c3e 35%,#9b9a96 50%,#d73c3e 65%,#b8242a)"></div>
</div>
<div class="abs rule" style="left:520px;top:2296px;width:88px"></div>
<div class="abs section-title" style="left:530px;top:2272px;width:580px;font-size:37px;line-height:49px">WHAT SHOULD I<br>BRING TO RENT A SPACE?</div>
<div class="abs rule" style="left:1033px;top:2296px;width:88px"></div>
<p class="abs body-text" style="left:530px;top:2383px;width:580px">Sed ut perspiciatis unde omnis iste natus error sit voluptatem accusantium doloremque laudantium, totam rem aperiam, eaque ipsa quae ab illo inventore veritatis et quasi architecto beatae vitae dicta sunt explicabo. Nemo enim ipsam voluptatem quia voluptas sit aspernatur aut odit aut fugit, sed quia consequuntur magni dolores.</p>
<div class="abs btn" style="left:717px;top:2596px;width:207px;height:57px">READ MORE</div>

<!-- Footer -->
<svg class="abs" style="left:0;top:2820px" width="1200" height="545"><polygon points="0,0 423,119 1200,0 1200,545 0,545" fill="var(--navy)"/></svg>
<div class="abs brand" style="left:66px;top:3076px;width:226px;color:#fff;font-size:27px">HARBOR LANE<small style="color:#fff;font-size:15px">SELF STORAGE</small></div>

<div class="abs footer-head" style="left:337px;top:2998px">QUICK LINKS</div>
<div class="abs footer-link" style="left:337px;top:3039px">Home</div>
<div class="abs footer-link" style="left:337px;top:3076px">Units</div>
<div class="abs footer-link" style="left:337px;top:3114px">Pay Online</div>
<div class="abs footer-link" style="left:337px;top:3152px">Contact Us</div>

<div class="abs footer-head" style="left:521px;top:2998px">ADDRESS</div>
<div class="abs" style="left:521px;top:3036px;font-size:18px;font-weight:600;color:#fff">Harbor Lane Self Storage</div>
<div class="abs footer-line" style="left:521px;top:3070px;width:290px;line-height:28px">
  <svg width="16" height="16" viewBox="0 0 16 16" style="margin-top:6px;flex:none"><path d="M8 1a5 5 0 0 1 5 5c0 4-5 9-5 9S3 10 3 6a5 5 0 0 1 5-5z" fill="#fff"/><circle cx="8" cy="6" r="2" fill="var(--navy)"/></svg>
  <span>2870 Linden Avenue Fairview, CA 90000</span>
</div>
<div class="abs footer-line" style="left:521px;top:3133px">
  <svg width="16" height="16" viewBox="0 0 16 16" style="margin-top:4px"><path d="M4 1c1 0 2 3 2 4s-2 1-2 2c1 2 2 3 4 4 1 0 1-2 2-2s4 1 4 2-1 3-3 3C6 14 2 10 2 4c0-2 1-3 2-3z" fill="#fff"/></svg>
  <span>1-800-555-0142</span>
</div>
<div class="abs footer-line" style="left:521px;top:3166px">
  <svg width="16" height="16" viewBox="0 0 16 16" style="margin-top:4px"><rect x="2" y="5" width="12" height="9" fill="#fff"/><rect x="5" y="1" width="6" height="5" fill="#fff"/></svg>
  <span>1-800-555-0142</span>
</div>
<div class="abs footer-line" style="left:521px;top:3199px">
  <svg width="16" height="16" viewBox="0 0 16 16" style="margin-top:4px"><rect x="1" y="3" width="14" height="10" fill="#fff"/><path d="M1 3l7 6 7-6" stroke="var(--navy)" fill="none"/></svg>
  <span>info@harborlanestorage.com</span>
</div>
<div class="abs footer-head" style="left:521px;top:3246px">OPENING TIMES</div>
<div class="abs footer-link" style="left:521px;top:3277px;font-size:15px">9:30 AM - 5:30 PM, 7 days a week</div>

<div class="abs" role="img" aria-label="Map showing the storage facility location" style="left:823px;top:3005px;width:302px;height:316px;background:linear-gradient(135deg,#eef0f2,#dfe3e8)"></div>

<div class="abs bottom-bar"></div>
<div class="abs" style="left:74px;top:3385px;font-size:14px;color:#fff">© Copyright 2022 CompanyName All Rights Reserved</div>
<div class="abs social" style="left:914px"></div>
<div class="abs social" style="left:960px"></div>
<div class="abs social" style="left:1006px"></div>
<div class="abs social" style="left:1052px"></div>
<div class="abs social" style="left:1098px"></div>

</body>
</html>
```